Business Card Design for Occupational Medicine Start Up Company

We need to design a professional business card. We are a healthcare company providing occupational medicine services to blue collar industries. We are professional, efficient and high quality service providers.

Target Market(s)

Blue Collar Industry: Shipbuilding, Ports, Trucking Companies; The Executives and Safety Officers for these companies

Industry/Entity Type

Healthcare

Contact Information for Business Card

Logo, Name, Title, Email, Phone

Other font styles liked:
• Please match our Brand Guide

Requirements
Must have
• Our Company Colors and Logo

```html
<!DOCTYPE html>
<html lang="en">
<head>
<meta charset="UTF-8">
<title>Harborline Clinics – Business Card</title>
<link href="https://fonts.googleapis.com/css2?family=Montserrat:wght@400;600;800&display=swap" rel="stylesheet">
<style>
  :root {
    --stage: #2a2a2c;
    --card-navy: #2b3486;
    --accent-orange: #f6b042;
    --accent-sky: #29a8e0;
    --ink-white: #ffffff;
  }
  * { box-sizing: border-box; margin: 0; padding: 0; }
  html, body { width: 1200px; height: 1015px; overflow: hidden; }
  body {
    background: var(--stage);
    font-family: "Montserrat", sans-serif;
    position: relative;
  }
  .card {
    position: absolute;
    width: 620px;
    height: 354px;
    background: var(--card-navy);
    box-shadow: 0 18px 40px rgba(0,0,0,0.55);
    color: var(--ink-white);
  }
  .card-front { left: 110px; top: 100px; }
  .card-back  { left: 470px; top: 560px; }

  /* Front */
  .front-brand {
    position: absolute; inset: 0;
    display: flex; flex-direction: column; align-items: center; justify-content: center;
    gap: 14px;
  }
  .brand-mark {
    width: 58px; height: 58px; border-radius: 50%;
    background: var(--accent-sky);
  }
  .brand-name {
    font-weight: 600; font-size: 34px; letter-spacing: 2px;
    color: var(--ink-white); text-transform: uppercase;
  }
  .brand-sub {
    font-weight: 600; font-size: 15px; letter-spacing: 9px;
    color: var(--ink-white); text-transform: uppercase; margin-top: -8px;
  }

  /* Back */
  .back-brand {
    position: absolute; right: 44px; top: 54px;
    display: flex; flex-direction: column; align-items: center; gap: 14px;
  }
  .back-brand .brand-mark { width: 130px; height: 130px; background: var(--accent-sky); }
  .back-brand .brand-name { font-size: 18px; letter-spacing: 3px; }

  .person { position: absolute; left: 44px; top: 176px; }
  .person-name {
    font-size: 22px; text-transform: uppercase; color: var(--accent-orange);
    font-weight: 800;
  }
  .person-name .surname { font-weight: 400; }
  .person-title {
    font-size: 13px; letter-spacing: 0.5px; text-transform: uppercase;
    color: var(--accent-sky); margin-top: 2px;
  }
  .contact-list { list-style: none; margin-top: 26px; }
  .contact-list li {
    display: flex; align-items: center; gap: 10px;
    font-size: 15px; line-height: 1.5; color: var(--ink-white);
  }
  .contact-list svg { width: 16px; height: 16px; flex: none; }
</style>
</head>
<body>

<section class="card card-front">
  <div class="front-brand">
    <span class="brand-mark"></span>
    <div class="brand-name">Harborline</div>
    <div class="brand-sub">Clinics</div>
  </div>
</section>

<section class="card card-back">
  <div class="back-brand">
    <span class="brand-mark"></span>
    <div class="brand-name">Harborline</div>
  </div>

  <div class="person">
    <div class="person-name">Daniel <span class="surname">Reyes</span></div>
    <div class="person-title">Managing Director</div>

    <ul class="contact-list">
      <li>
        <svg viewBox="0 0 24 24" aria-hidden="true"><path fill="var(--accent-orange)" d="M6.6 10.8a15 15 0 0 0 6.6 6.6l2.2-2.2a1 1 0 0 1 1-.25 11.4 11.4 0 0 0 3.6.57 1 1 0 0 1 1 1V20a1 1 0 0 1-1 1A17 17 0 0 1 3 4a1 1 0 0 1 1-1h3.5a1 1 0 0 1 1 1c0 1.25.2 2.45.57 3.57a1 1 0 0 1-.25 1z"/></svg>
        044-555 010 234
      </li>
      <li>
        <svg viewBox="0 0 24 24" aria-hidden="true"><rect x="2" y="5" width="20" height="14" rx="1" fill="var(--accent-orange)"/><path d="M2 6l10 7 10-7" stroke="var(--card-navy)" stroke-width="2" fill="none"/></svg>
        info@harborlinecare.com
      </li>
      <li>
        <svg viewBox="0 0 24 24" aria-hidden="true"><g fill="none" stroke="var(--accent-orange)" stroke-width="2"><circle cx="12" cy="12" r="9"/><ellipse cx="12" cy="12" rx="4" ry="9"/><path d="M3 12h18M5 7h14M5 17h14"/></g></svg>
        www.harborlinecare.com
      </li>
    </ul>
  </div>
</section>

</body>
</html>
```